Norrell Advisory WA Business Card

Create an interesting, eye catching and colourful two sided business card. We are a business consulting operation assisting SME's improve all areas of their business. We provide consulting services to assist SME's to create a culture of continuous improvement, making a positive difference in the business. Our tag line is Small changes, big rewards. We want to create a well recognised, innovative brand that can be continued throughout our website, social media and email correspondence.

Target Market(s)

Small to Medium Enterprise Business Owners

Industry/Entity Type

Business Consultant

Contact Information for Business Card

Name of Business: Norrell Advisory - Steady steps strong results
Derek Holloway Ph 0407385510 Megan Holloway Ph 0407913847
Email norrelladvisorywa@mailbox-example.com
Web address TBA
FaceBook page TBA

BACKSIDE OF CARD

Providing assistance with:

• Organisation & Efficiency
• Revenue generation & Marketing
• Financial Management
• Production quality & delivery
• Systems & Process documentation
• Exit Strategy

Font styles to use
Other font styles liked:
• Calibri

Colors

Designer to choose colors to be used in the design.

Requirements
Must have
• Calibri font

```html
<!DOCTYPE html>
<html lang="en">
<head>
<meta charset="utf-8">
<title>Norrell Advisory WA Business Card</title>
<link rel="stylesheet" href="https://fonts.googleapis.com/css2?family=Open+Sans:wght@400;600;700&family=Carlito:wght@400;700&display=swap">
<style>
  :root {
    --page: #e4e4e4;
    --card-front: #ffffff;
    --ink-dark: #2f2f2f;
    --ink-mid: #555555;
    --ink-soft: #4a4a4a;
    --brand-blue: #1a7bbf;
    --accent-blue: #1f8fd0;
    --accent-red: #e2453c;
    --accent-green: #7cb342;
    --accent-yellow: #f3b53a;
    --text-light: #ffffff;
  }
  * { margin: 0; padding: 0; box-sizing: border-box; }
  html, body {
    width: 1125px;
    height: 1200px;
    overflow: hidden;
    background: var(--page);
  }
  body { position: relative; font-family: "Open Sans", Arial, sans-serif; }

  .card {
    position: absolute;
    left: 171px;
    width: 826px;
    height: 470px;
    border-radius: 24px;
    overflow: hidden;
  }
  .card--front { top: 106px; background: var(--card-front); }
  .card--back { top: 639px; }

  .brand {
    position: absolute;
    right: 57px;
    top: 72px;
    text-align: right;
  }
  .brand__name {
    display: flex;
    align-items: center;
    justify-content: flex-end;
    gap: 14px;
    font-weight: 700;
    font-size: 36px;
    line-height: 1;
    color: var(--ink-dark);
    letter-spacing: 0.3px;
  }
  .brand__square {
    width: 30px;
    height: 30px;
    background: var(--brand-blue);
  }
  .brand__tagline {
    margin-top: 4px;
    font-size: 20px;
    font-weight: 400;
    letter-spacing: 2px;
    color: var(--ink-mid);
  }

  .contacts {
    position: absolute;
    right: 57px;
    top: 168px;
    text-align: right;
  }
  .contact + .contact { margin-top: 16px; }
  .contact__name {
    font-size: 28px;
    font-weight: 600;
    line-height: 1.1;
    color: var(--brand-blue);
  }
  .contact__phone {
    margin-top: 2px;
    font-size: 16px;
    font-weight: 700;
    color: var(--ink-mid);
  }

  .colour-rule {
    position: absolute;
    left: 61px;
    right: 57px;
    top: 378px;
    display: flex;
    gap: 3px;
    height: 4px;
  }
  .colour-rule span { flex: 1; }
  .colour-rule .blue { background: linear-gradient(90deg, #1a6fae, #7cc1e4); }
  .colour-rule .red { background: var(--accent-red); }
  .colour-rule .green { background: linear-gradient(90deg, #6aa83a, #9ccc50); }
  .colour-rule .yellow { background: linear-gradient(90deg, var(--accent-yellow), #f2de4a); }

  .contact-line {
    position: absolute;
    right: 57px;
    top: 400px;
    font-size: 15px;
    color: var(--ink-soft);
    white-space: nowrap;
  }

  .back-pattern {
    position: absolute;
    inset: 0;
    background: linear-gradient(135deg, #2f2a28 0%, #262a2d 50%, #2e2b24 100%);
  }

  .services {
    position: absolute;
    right: 57px;
    top: 128px;
    text-align: right;
  }
  .services__title {
    font-size: 26px;
    font-weight: 600;
    color: var(--brand-blue);
    margin-bottom: 10px;
  }
  .services__list { list-style: none; }
  .services__item {
    display: flex;
    align-items: center;
    justify-content: flex-end;
    gap: 14px;
    height: 26.3px;
    font-family: "Carlito", "Calibri", sans-serif;
    font-size: 19px;
    color: var(--text-light);
  }
  .services__bullet {
    width: 11px;
    height: 11px;
    border-radius: 50%;
    background: var(--accent-blue);
  }
</style>
</head>
<body>

  <section class="card card--front" aria-label="Business card front">
    <div class="brand">
      <div class="brand__name"><span class="brand__square" aria-hidden="true"></span>NORRELL ADVISORY</div>
      <div class="brand__tagline">STEADY STEPS STRONG RESULTS</div>
    </div>

    <div class="contacts">
      <div class="contact">
        <div class="contact__name">Derek Holloway</div>
        <div class="contact__phone">0407385510</div>
      </div>
      <div class="contact">
        <div class="contact__name">Megan Holloway</div>
        <div class="contact__phone">0407913847</div>
      </div>
    </div>

    <div class="colour-rule" aria-hidden="true">
      <span class="blue"></span><span class="red"></span><span class="green"></span><span class="yellow"></span>
    </div>

    <p class="contact-line">norrelladvisorywa@mailbox-example.com | norrelladvisorywa.com | FB: norrelladvisorywa</p>
  </section>

  <section class="card card--back" aria-label="Business card back">
    <div class="back-pattern" role="img" aria-label="Dark muted jigsaw puzzle piece pattern in deep red, blue, green and olive tones"></div>
    <div class="services">
      <h2 class="services__title">Providing assistance with</h2>
      <ul class="services__list">
        <li class="services__item">Organisation &amp; Efficiency<span class="services__bullet"></span></li>
        <li class="services__item">Revenue generation &amp; Marketing<span class="services__bullet"></span></li>
        <li class="services__item">Financial Management<span class="services__bullet"></span></li>
        <li class="services__item">Production quality &amp; delivery<span class="services__bullet"></span></li>
        <li class="services__item">Systems &amp; Process documentation<span class="services__bullet"></span></li>
        <li class="services__item">Exit Strategy<span class="services__bullet"></span></li>
      </ul>
    </div>
  </section>

</body>
</html>
```